Explosive, chemical reaction of creativity!

Web design for a digital marketing company. The unconventional is encouraged!
This is for a cool, young, geographically diverse company (sketchhive... you are all part of our team!!!)... we build websites but our real specialty is "search experience optimization".... creating conversion focused content, SEO (including content), and social media.

Target Market(s)

small to medium size businesses, law firms, medical practices, municipalities

Industry/Entity Type

Marketing

Number of Pages Required

2 page

Requirements
Must have
• WOW
• something different and special... we've been playing with a science theme (www.fernquillmedia.marketing) but we are open to different looks, layouts, etc.
• we nee a homepage design and an interior page design
• content needs to include: Marketing Catalysts (about us), Our Formula (services), Chemical Reactions(Results/Our Clients),
• FREE Online Prism Check
• Let us put together an objective snapshot of your digital presence for you.
Nice to have
• we are open to the use of background video (chemical reaction???)
• we are open to cool and different imagery
Should not have
• template look like most other websites

```html
<!DOCTYPE html>
<html lang="en">
<head>
<meta charset="utf-8">
<title>Fernquill Media — Digital Marketing</title>
<link rel="stylesheet" href="https://fonts.googleapis.com/css2?family=Roboto:wght@300;400;500;700&display=swap">
<style>
:root{
  --navy:#1c3d5e;
  --band:#1c60a8;
  --btn:#1f4f7c;
  --accent:#2a8ad8;
  --text:#555d66;
  --muted:#8a929a;
  --light:#f4f5f6;
  --white:#ffffff;
  --hero-a:#04121f;
  --hero-b:#0b3350;
}
*{box-sizing:border-box;margin:0;padding:0}
html,body{width:1200px;height:3340px;overflow:hidden}
body{font-family:"Roboto",Arial,sans-serif;color:var(--text);background:var(--white);position:relative}
.abs{position:absolute}
.wordmark{font-weight:700;font-size:15px;letter-spacing:2px;color:var(--navy);text-transform:uppercase;display:flex;align-items:center;gap:8px;white-space:nowrap}
.wordmark i{width:12px;height:12px;background:var(--accent);display:block}

.site-header{left:0;top:0;width:1200px;height:80px;background:var(--white)}
.site-header .wordmark{position:absolute;left:174px;top:31px}
.main-nav{position:absolute;right:172px;top:34px;display:flex;gap:24px;font-size:11px;text-transform:uppercase;color:#333}
.main-nav .active{color:var(--accent)}

.hero{left:0;top:80px;width:1200px;height:488px;background:linear-gradient(180deg,var(--hero-a),var(--hero-b) 55%,var(--hero-a))}
.hero h1{position:absolute;top:240px;width:100%;text-align:center;color:var(--white);font-weight:300;font-size:32px;letter-spacing:.5px}
.hero p{position:absolute;top:292px;width:100%;text-align:center;color:#d6e4ef;font-size:11px}
.hero-dots{position:absolute;top:425px;left:577px;display:flex;gap:6px}
.hero-dots span{width:7px;height:7px;border-radius:50%;background:#fff;opacity:.95}
.hero-dots span:first-child{opacity:.45}

.data-intro{left:0;top:568px;width:1200px;height:334px;background:var(--light);text-align:center}
.data-intro h2{position:absolute;top:53px;width:100%;font-size:37px;font-weight:500;color:var(--navy)}
.data-intro .lead{position:absolute;top:99px;width:100%;font-size:13px}
.data-intro .body{position:absolute;top:158px;left:182px;width:846px;font-size:10.5px;line-height:17px}
.btn{display:inline-block;background:var(--btn);color:#fff;font-size:11px;text-transform:uppercase;text-align:center;font-weight:500;white-space:nowrap}
.data-intro .btn{position:absolute;left:539px;top:249px;width:122px;height:34px;line-height:34px}

.stats{left:0;top:902px;width:1200px;height:300px;background:var(--band);color:#fff}
.stat{position:absolute;top:70px;width:200px;margin-left:-100px;text-align:center}
.stat svg{display:block;margin:0 auto}
.stat strong{display:block;font-size:46px;font-weight:500;margin-top:10px}
.stat span{display:block;font-size:11px;line-height:16px;margin-top:8px;color:#dce9f6}

.formula{left:0;top:1202px;width:1200px;height:690px}
.phone{position:absolute;left:292px;top:85px;width:249px;height:521px;border-radius:40px;background:#e9ebee;border:3px solid #d3d6da;box-shadow:0 14px 30px rgba(0,0,0,.12)}
.phone .screen{position:absolute;left:14px;top:62px;width:215px;height:380px;background:#fff;border:1px solid #ccc;display:flex;align-items:center;justify-content:center}
.phone .home{position:absolute;left:101px;top:462px;width:42px;height:42px;border-radius:50%;border:2px solid #c7cbd0}
.phone .speaker{position:absolute;left:92px;top:32px;width:60px;height:6px;border-radius:3px;background:#c7cbd0}
.formula h2{position:absolute;left:579px;top:86px;font-size:36px;line-height:42px;font-weight:500;color:var(--navy);white-space:nowrap}
.formula .lead{position:absolute;left:579px;top:197px;font-size:13px;white-space:nowrap}
.service{position:absolute;left:575px;width:440px;height:90px}
.service svg{position:absolute;left:0;top:0}
.service h3{position:absolute;left:106px;top:-4px;font-size:20px;font-weight:400;color:var(--navy)}
.service p{position:absolute;left:106px;top:32px;width:290px;font-size:10.5px;line-height:16px;color:var(--muted)}

.offer{position:absolute;left:0;top:0;width:1200px;height:3340px;pointer-events:none}
.photo{position:absolute}
.photo-lab{left:174px;top:1932px;width:416px;height:230px;background:linear-gradient(135deg,#e7e9ed,#b9c3cf 60%,#d8dde3)}
.photo-laptop{left:610px;top:2239px;width:416px;height:230px;background:linear-gradient(160deg,#eef0f2,#9aa1a9 55%,#d6d9dd)}
.offer-head{position:absolute;width:420px;font-size:17px;color:#333;line-height:26px}
.offer-head svg{position:absolute;left:0;top:6px}
.offer-text{position:absolute;width:420px;font-size:10.5px;line-height:15.5px;color:var(--muted)}
.offer .btn{position:absolute;height:38px;line-height:38px}

.news-title{left:0;top:2550px;width:1200px;text-align:center;font-size:34px;color:var(--accent);font-weight:400}
.card{position:absolute;top:2640px;width:270px}
.card .thumb{width:270px;height:185px}
.card h3{margin-top:22px;font-size:20px;line-height:26px;font-weight:500;color:#333}
.card p{margin-top:14px;font-size:10.5px;line-height:15.5px;color:var(--muted)}
.card .btn{margin-top:33px;background:var(--accent);width:62px;height:25px;line-height:25px;text-transform:none;font-size:10px}
.date-badge{position:absolute;left:94px;top:41px;width:90px;height:90px;border-radius:50%;background:var(--accent);color:#fff;font-size:13px;font-weight:700;text-align:center;display:flex;align-items:center;justify-content:center;line-height:16px}

.site-footer{left:0;top:3110px;width:1200px;height:230px;background:var(--light);text-align:center}
.site-footer .wordmark{position:absolute;left:0;width:100%;justify-content:center;top:46px}
.social{position:absolute;top:106px;width:100%;display:flex;justify-content:center;gap:14px}
.social span{width:16px;height:16px;border-radius:50%;background:var(--accent)}
.foot-nav{position:absolute;top:157px;width:100%;font-size:10px;color:#333;text-transform:uppercase;letter-spacing:.3px}
.foot-nav b{font-weight:400;margin:0 12px;color:#888}
.copy{position:absolute;top:192px;width:100%;font-size:9.5px;color:#444;text-transform:uppercase}
</style>
</head>
<body>

<header class="site-header abs">
  <div class="wordmark"><i></i>Fernquill Media</div>
  <nav class="main-nav">
    <span class="active">Home</span><span>Marketing Catalysts</span><span>Our Formula</span><span>Chemical Reactions</span><span>Contact Us</span>
  </nav>
</header>

<section class="hero abs" role="img" aria-label="Glowing blue digital data streams background">
  <h1>IT'S NOT ROCKET SCIENCE, IT'S FERNQUILL DIGITAL SCIENCE!</h1>
  <p>Sales is the chemical reaction that results from "our formula" which is the right combination of our digital marketing services.</p>
  <div class="hero-dots"><span></span><span></span><span></span><span></span></div>
</section>

<section class="data-intro abs">
  <h2>USING DATA FOR SUCCESS</h2>
  <p class="lead">Search Engine Optimization has been replaced with Search Experience Optimization</p>
  <p class="body">SALES is the end result of everything we do. It is why companies exists. It's why we market. It's why your business is online. Our job is to help you maximize your opportunity online to build your brand, get found by new customers and, ultimately, generate SALES! There's been a lot of talk the last few years about SEO, Search Engine Optimization. We believe that Search Engine Optimization has now been replaced with Search Experience Optimization.</p>
  <span class="btn">Learn More</span>
</section>

<section class="stats abs">
  <div class="stat" style="left:269px">
    <svg width="36" height="36" viewBox="0 0 36 36"><circle cx="15" cy="15" r="10" fill="none" stroke="#fff" stroke-width="4"/><line x1="22" y1="22" x2="32" y2="32" stroke="#fff" stroke-width="5" stroke-linecap="round"/></svg>
    <strong>93%</strong><span>Online experiences begin<br>with a search engine</span>
  </div>
  <div class="stat" style="left:487px">
    <svg width="36" height="36" viewBox="0 0 36 36"><g fill="none" stroke="#fff" stroke-width="4"><rect x="4" y="4" width="14" height="14" rx="7"/><rect x="18" y="18" width="14" height="14" rx="7"/></g><line x1="13" y1="13" x2="23" y2="23" stroke="#fff" stroke-width="4"/></svg>
    <strong>70%</strong><span>Of the links search users<br>click on are organic</span>
  </div>
  <div class="stat" style="left:703px">
    <svg width="36" height="36" viewBox="0 0 36 36"><rect x="6" y="7" width="24" height="16" fill="none" stroke="#fff" stroke-width="3"/><rect x="2" y="26" width="32" height="4" fill="#fff"/></svg>
    <strong>70%</strong><span>Of US population has at least<br>one social networking profile</span>
  </div>
  <div class="stat" style="left:926px">
    <svg width="36" height="36" viewBox="0 0 36 36"><polyline points="3,4 3,32 34,32" fill="none" stroke="#fff" stroke-width="3"/><polyline points="8,26 16,17 22,22 32,10" fill="none" stroke="#fff" stroke-width="3.5"/><polygon points="26,9 33,8 32,15" fill="#fff"/></svg>
    <strong>50%</strong><span>Of companies are using digital<br>marketing but don't have a plan</span>
  </div>
</section>

<section class="formula abs">
  <div class="phone">
    <div class="speaker"></div>
    <div class="screen"><div class="wordmark" style="font-size:12px"><i></i>Fernquill Media</div></div>
    <div class="home"></div>
  </div>
  <h2>THE PERFECT DIGITAL<br>MARKETING FORMULA!</h2>
  <p class="lead">Get the right message in front of the right people</p>

  <div class="service" style="top:285px">
    <svg width="60" height="52" viewBox="0 0 60 52"><rect x="2" y="4" width="56" height="34" rx="3" fill="var(--btn)"/><rect x="7" y="9" width="46" height="24" fill="#fff"/><rect x="24" y="38" width="12" height="8" fill="var(--btn)"/><rect x="16" y="46" width="28" height="4" fill="var(--btn)"/></svg>
    <h3>Website</h3>
    <p>You've got 10 seconds to grab the attention of a site viewer. We build for appearance, content, and functionality. It's a conversion causal nexus!</p>
  </div>
  <div class="service" style="top:418px">
    <svg width="60" height="56" viewBox="0 0 60 56"><path d="M10 2h28l12 12v40H10z" fill="var(--btn)"/><g fill="#fff"><rect x="17" y="22" width="26" height="3"/><rect x="17" y="30" width="26" height="3"/><rect x="17" y="38" width="26" height="3"/></g></svg>
    <h3>Content</h3>
    <p>Content is the most powerful element of our formula... it creates need, provokes emotion and sparks action.</p>
  </div>
  <div class="service" style="top:534px">
    <svg width="60" height="52" viewBox="0 0 60 52"><ellipse cx="24" cy="20" rx="20" ry="14" fill="var(--btn)"/><polygon points="10,30 6,42 20,32" fill="var(--btn)"/><ellipse cx="38" cy="30" rx="17" ry="12" fill="none" stroke="var(--btn)" stroke-width="4"/></svg>
    <h3>Social</h3>
    <p>We are obsessed with the latest trends and are always testing new ways to cultivate both following and engagement.</p>
  </div>
</section>

<section class="offer">
  <div class="photo photo-lab" role="img" aria-label="Hands working with a tablet beside medical and data graphics"></div>
  <h3 class="offer-head" style="left:610px;top:1926px;padding-left:38px;font-weight:400">
    <svg width="18" height="14" viewBox="0 0 18 14"><polyline points="2,7 7,12 16,2" fill="none" stroke="var(--accent)" stroke-width="3"/></svg>
    FREE Online Prism Check
  </h3>
  <p class="offer-text" style="left:610px;top:1980px">Lorem Ipsum is simply dummy text of the printing and typesetting industry. Lorem Ipsum has been the industry's standard dummy text ever since the 1500s, when an unknown printer took a galley of type and scrambled it to make a type specimen book. It has survived not only five centuries.<br>Lorem Ipsum is simply dummy text of the printing and typesetting industry. Lorem Ipsum has been the industry's standard dummy text ever.</p>
  <span class="btn" style="left:610px;top:2124px;width:125px">Book Now</span>

  <h3 class="offer-head" style="left:174px;top:2234px;padding-left:45px;font-weight:400">
    <svg width="18" height="14" viewBox="0 0 18 14"><polyline points="2,7 7,12 16,2" fill="none" stroke="var(--accent)" stroke-width="3"/></svg>
    Let us put together an objective<br>snapshot of your digital presence for you.
  </h3>
  <p class="offer-text" style="left:174px;top:2300px">Lorem Ipsum is simply dummy text of the printing and typesetting industry. Lorem Ipsum has been the industry's standard dummy text ever since the 1500s, when an unknown printer took a galley of type and scrambled it to make a type specimen book. It has survived not only five centuries.<br>Lorem Ipsum is simply dummy text of the printing and typesetting industry. Lorem Ipsum has been the industry's standard dummy text ever.</p>
  <span class="btn" style="left:174px;top:2431px;width:151px">Create Snapshot</span>
  <div class="photo photo-laptop" role="img" aria-label="Hands typing on a laptop on a bright desk"></div>
</section>

<h2 class="news-title abs">NEWS</h2>

<article class="card" style="left:174px">
  <div class="thumb" style="position:relative;background:linear-gradient(135deg,#2a2a2a,#0e0e0e)" role="img" aria-label="Dark portrait photo for a marketing article">
    <div class="date-badge">MARCH<br>10TH<br>2016</div>
  </div>
  <h3>5 Killer Marketing Lessons From Tower Of Tiles</h3>
  <p>After spending an embarrassing amount of time binge watching Tower Of Tiles this past weekend, I have arrived at the conclusion that there is a lot to learn about marketing from the Wexfords.</p>
  <span class="btn">Read More</span>
</article>
<article class="card" style="left:465px">
  <div class="thumb" style="background:linear-gradient(180deg,#3a9aa0,#2e6f77 60%,#c9a36a)" role="img" aria-label="Group of young people with a trend banner"></div>
  <h3>5 Killer Marketing Lessons From Tower Of Tiles</h3>
  <p>After spending an embarrassing amount of time binge watching Tower Of Tiles this past weekend, I have arrived at the conclusion that there is a lot to learn about marketing from the Wexfords.</p>
  <span class="btn">Read More</span>
</article>
<article class="card" style="left:757px">
  <div class="thumb" style="background:linear-gradient(135deg,#1a1a1a,#3a1a12 60%,#b8431e)" role="img" aria-label="Basketball hoop with a sports marketing banner"></div>
  <h3>5 Killer Marketing Lessons From Tower Of Tiles</h3>
  <p>After spending an embarrassing amount of time binge watching Tower Of Tiles this past weekend, I have arrived at the conclusion that there is a lot to learn about marketing from the Wexfords.</p>
  <span class="btn">Read More</span>
</article>

<footer class="site-footer abs">
  <div class="wordmark"><i></i>Fernquill Media</div>
  <div class="social"><span></span><span></span><span></span></div>
  <div class="foot-nav">Home<b>|</b>Marketing Catalysts<b>|</b>Our Formula<b>|</b>Chemical Reactions<b>|</b>Contact Us</div>
  <div class="copy">© 2016 Company Name | All Rights Reserved</div>
</footer>

</body>
</html>
```